Whitcombe Business Card Design

The name of the business is Dario Whitcombe, CPA LLC
The service that we offer is Accounting, Tax & Consulting Services. I need it to have the following items:
Dario Whitcombe, Principal
Phone Number
Email Address
Physical Address

I have attached the company logo, one in black and one in white. Please provide a design in black background and the other in white background. Please include "Accounting, Tax & Consulting Services". I want the business card to be clean and very professional.

```html
<!DOCTYPE html>
<html lang="en">
<head>
<meta charset="UTF-8">
<title>Dario Whitcombe, CPA LLC — Business Card</title>
<link rel="stylesheet" href="https://fonts.googleapis.com/css2?family=Montserrat:wght@500;600;700&family=Poppins:wght@400;500;600&display=swap">
<style>
  :root {
    --ink: #0a0a0a;
    --crimson: #9c171c;
    --paper: #ffffff;
    --charcoal: #2f2f33;
    --slate: #8a8a8f;
    --backdrop: #3a3a3c;
  }
  * { box-sizing: border-box; margin: 0; padding: 0; }
  html, body { width: 1200px; height: 1015px; overflow: hidden; }
  body {
    background: var(--backdrop);
    display: flex;
    flex-direction: column;
    align-items: center;
    justify-content: center;
    gap: 40px;
    font-family: "Poppins", sans-serif;
  }
  .card {
    width: 760px;
    height: 434px;
    position: relative;
    overflow: hidden;
    box-shadow: 0 14px 30px rgba(0,0,0,0.45);
  }

  /* Front */
  .card--front { background: var(--ink); }
  .front__brand {
    position: absolute;
    top: 0; left: 0; right: 0;
    height: 338px;
    display: flex;
    flex-direction: column;
    align-items: center;
    justify-content: center;
    gap: 12px;
  }
  .brand-mark {
    width: 58px; height: 58px;
    border: 7px solid var(--paper);
    flex: none;
  }
  .brand-name {
    font-family: "Montserrat", sans-serif;
    font-weight: 600;
    font-size: 34px;
    letter-spacing: 1px;
    color: var(--paper);
    text-transform: uppercase;
    white-space: nowrap;
  }
  .brand-tagline {
    font-family: "Montserrat", sans-serif;
    font-weight: 500;
    font-size: 18px;
    letter-spacing: 5px;
    color: var(--slate);
    text-transform: uppercase;
    white-space: nowrap;
  }
  .front__band {
    position: absolute;
    left: 0; right: 0; bottom: 0;
    height: 96px;
    background: var(--crimson);
    display: flex;
    align-items: center;
    justify-content: center;
  }
  .services {
    font-family: "Montserrat", sans-serif;
    font-weight: 600;
    font-size: 19px;
    letter-spacing: 1px;
    color: var(--paper);
    text-transform: uppercase;
  }

  /* Back */
  .card--back { background: var(--crimson); }
  .back__header {
    height: 150px;
    background: var(--paper);
    display: flex;
    align-items: center;
    padding-left: 60px;
    gap: 26px;
  }
  .card--back .brand-mark {
    width: 66px; height: 66px;
    border-color: var(--charcoal);
  }
  .back__header .brand-text { display: flex; flex-direction: column; gap: 6px; }
  .card--back .brand-name { color: var(--charcoal); font-size: 33px; }
  .card--back .brand-tagline { font-size: 19px; }
  .back__details {
    position: absolute;
    top: 150px; left: 0; right: 0; bottom: 0;
    display: flex;
    flex-direction: column;
    align-items: center;
    justify-content: center;
    color: var(--paper);
    text-align: center;
  }
  .person__name { font-weight: 600; font-size: 24px; line-height: 1.1; }
  .person__role { font-size: 17px; margin-bottom: 10px; }
  .divider {
    display: flex; align-items: center; gap: 14px; margin: 4px 0 8px;
  }
  .divider__rule { width: 90px; height: 1.5px; background: var(--paper); }
  .divider__icons { display: flex; gap: 6px; }
  .icon-box {
    width: 26px; height: 22px;
    border: 1.5px solid var(--paper);
    display: flex; align-items: center; justify-content: center;
  }
  .contact { font-size: 18px; line-height: 1.45; }
  .rule-short { width: 90px; height: 1.5px; background: var(--paper); margin: 10px 0; }
  .address { font-size: 18px; }
</style>
</head>
<body>

  <section class="card card--front">
    <div class="front__brand">
      <div class="brand-mark"></div>
      <div class="brand-name">Dario Whitcombe, CPA LLC</div>
      <div class="brand-tagline">Certified Public Accountant</div>
    </div>
    <div class="front__band">
      <p class="services">Accounting, Tax &amp; Consulting Services</p>
    </div>
  </section>

  <section class="card card--back">
    <header class="back__header">
      <div class="brand-mark"></div>
      <div class="brand-text">
        <div class="brand-name">Dario Whitcombe, CPA LLC</div>
        <div class="brand-tagline">Certified Public Accountant</div>
      </div>
    </header>
    <div class="back__details">
      <p class="person__name">Dario Whitcombe</p>
      <p class="person__role">Principal</p>
      <div class="divider">
        <span class="divider__rule"></span>
        <span class="divider__icons">
          <span class="icon-box">
            <svg width="14" height="14" viewBox="0 0 24 24" fill="none" stroke="#fff" stroke-width="2.4" aria-hidden="true"><path d="M5 3h4l2 5-3 2a12 12 0 0 0 6 6l2-3 5 2v4a2 2 0 0 1-2 2A17 17 0 0 1 3 5a2 2 0 0 1 2-2z"/></svg>
          </span>
          <span class="icon-box">
            <svg width="16" height="12" viewBox="0 0 24 18" fill="none" stroke="#fff" stroke-width="2.2" aria-hidden="true"><rect x="1.5" y="1.5" width="21" height="15"/><path d="M1.5 1.5l10.5 9 10.5-9"/></svg>
          </span>
        </span>
        <span class="divider__rule"></span>
      </div>
      <p class="contact">555-018 462 730<br>info@whitcombecpa.com</p>
      <span class="rule-short"></span>
      <p class="address">218 Harbor Lane, Suite 4, Millbrook, OR 97402</p>
    </div>
  </section>

</body>
</html>
```